A website where experts collaborate on your project

I am building a new website where experts (yes, like designers) collaborate on projects with the project owner. More minds = more collaboration = better end product. Please see Pelmora(dot)com for a quick landing page I created for collaborating on presentations (although there will be many project types offered)

I am looking for a DESIGNER LONG TERM, but for now, just need initial mock ups to show the web programmers.

I have 21 Word documents loosely designed, what I would like to see here is a theme. Please DO NOT GO OFF WHAT YOU CURRENTLY SEE AT PELMORA. What is up now is only a quick landing page.

You can view a Word doc of the homepage here:
https://www.filevanta.com/s/qx83kdm2/home.docx?dl=0

WHAT AM I LOOKING FOR?
A clean, well designed theme.

Here is a link to the logo:
https://www.filevanta.com/s/mr47tpz9/logo%20-%20horizontal.tif?dl=0
-----------------------------------------
Here are a few sites I like the design of and what I like about them:
www.quenbrook.com-all around my favorite, beautiful graphics, clean layout, bold use of colors on a dark background
Ravelto.com- clean layout, The use of humans and bubble style elements.
Mintharbor.com :) clean, bold, unique pop art style but professional
plumevault.com - From the unique colors and artwork and the ability of that art to not interfere with the important elements of the site
sparkwidgets.com-clean, nice colors, well organized and separated sections.
www.dunmereco.com-love the font, use of colors and sectionalized style

All in all, I am not picky and open to so many styles. I would ultimately like the designer I pick to design all 21 pages.
Updates

Hello everyone,Moving forward, I would like you all to pay special attention to the section in my brief titled "Here are a few sites I like the design of and what I like about them". Please see below, I handpicked each one of these as sites I really like. Thank you.Here are a few sites I like the design of and what I like about them:Ravelto.com- clean layout, The use of humans and bubble style elements.Mintharbor.com :) clean, bold, unique pop art style but professionalwriteraccess.com - From the unique colors and artwork and the ability of that art to not interfere with the important elements of the sitegrowthgeeks.com-clean, nice colors, well organized and separated sections.www.dunmereco.com-love the font, use of colors and sectionalized stylewww.quenbrook.com-beautiful graphics, clean layout, bold use of colors----------------------------------------- Added Tuesday, November 24, 2015

I updated the homepage, you can see it here:https://www.dropbox.com/s/kwlkbsookq3cg2m/1new%20homepage.docx?dl=0I am modeling it after my favorite designed site: triplelift.comI love the dark colors with the orange glowing style boldness of the buttons. It's real clean too. Added Tuesday, November 24, 2015

Target Market(s)

small business owners, marketers, freelancer writers, graphic designers,

Industry/Entity Type

Building

Number of Pages Required

5+ page

Requirements
Must have
• I can't think of anything the project must have.
Nice to have
• WHAT AM I LOOKING FOR?
• A clean, well designed theme. I had a designer do a bit of work putting elements together, I found it to be very plain, but I like the Application Page (https://www.filevanta.com/s/jb19ckr3/Pelmora-Website.ai?dl=0)
• Here is a link to the logo:
• https://www.filevanta.com/s/mr47tpz9/logo%20-%20horizontal.tif?dl=0
• Here are a few sites I like the design of and what I like about them:
• Ravelto.com- clean layout, The use of humans and bubble style elements.
• Mintharbor.com :) clean, bold, unique pop art style but professional
• plumevault.com - From the unique colors and artwork and the ability of that art to not interfere with the important elements of the site
• sparkwidgets.com-clean, nice colors, well organized and separated sections.
• www.dunmereco.com-love the font, use of colors and sectionalized style
• www.quenbrook.com-beautiful graphics, clean layout, bold use of colors
• -----------------------------------------
Should not have
• out of the boxed, templated style website. I want this site to be memorable and not look like a thousand others

```html
<!DOCTYPE html>
<html lang="en">
<head>
<meta charset="utf-8">
<title>Pelmora — Experts collaborating on your project</title>
<link href="https://fonts.googleapis.com/css2?family=Open+Sans:wght@400;600;700&display=swap" rel="stylesheet">
<style>
:root{
  --orange:#f7931e;
  --orange-dark:#e8820c;
  --dark:#2b2b2b;
  --dark-2:#333333;
  --teal:#4aa3b8;
  --ink:#333333;
  --muted:#777777;
  --line:#d6d6d6;
  --panel:#f2f2f2;
  --white:#ffffff;
}
*{box-sizing:border-box;margin:0;padding:0}
html,body{width:1200px;height:2233px;overflow:hidden}
body{position:relative;background:var(--white);font-family:"Open Sans",Arial,sans-serif;color:var(--ink)}
.abs{position:absolute}

/* header */
.site-header{position:absolute;left:0;top:0;width:1200px;height:135px;background:var(--dark)}
.search{position:absolute;left:98px;top:51px;width:127px;height:41px;background:var(--white);border-radius:3px;font-size:12px;color:#444;padding:12px 0 0 15px}
.search svg{position:absolute;right:14px;top:13px}
.notice{position:absolute;left:338px;top:13px;width:643px;height:36px;background:#3d3d3d;border-radius:2px;font-size:12px;color:#bdbdbd;display:flex;align-items:center}
.notice-tag{background:var(--teal);color:var(--white);height:36px;padding:0 16px;display:flex;align-items:center;margin-right:15px;border-radius:2px 0 0 2px}
.nav{position:absolute;left:336px;top:71px;display:flex;align-items:center;height:36px;font-size:12.5px;color:var(--white)}
.nav a{color:var(--white);text-decoration:none;margin-right:30px}
.nav .active{background:var(--orange);height:36px;width:68px;display:flex;align-items:center;justify-content:center;border-radius:2px;margin-right:24px}
.brand{position:absolute;display:flex;align-items:center;gap:12px;font-weight:700;color:var(--orange)}
.brand-dot{border-radius:50%;background:var(--orange)}
.header-brand{left:860px;top:48px;font-size:34px}
.header-brand .brand-dot{width:48px;height:48px}

/* hero */
.hero{position:absolute;left:0;top:135px;width:1200px;height:496px;background:linear-gradient(160deg,#6b4a32 0%,#4f3726 40%,#3e2c20 70%,#5a4634 100%)}
.hero-shade{position:absolute;inset:0;background:rgba(0,0,0,.28)}
.hero h1{position:absolute;top:120px;width:100%;text-align:center;font-size:54px;font-weight:700;color:var(--orange);letter-spacing:.5px}
.hero p{position:absolute;top:190px;width:100%;text-align:center;font-size:31px;color:var(--white)}
.btn{background:var(--orange);color:var(--white);font-weight:700;border-radius:3px;display:flex;align-items:center;justify-content:center}
.hero .btn{position:absolute;left:536px;top:260px;width:128px;height:47px;font-size:15px}
.dots{position:absolute;top:434px;left:572px;display:flex;gap:8px}
.dots i{width:8px;height:8px;border-radius:50%;background:rgba(255,255,255,.6)}
.dots i.on{background:var(--orange)}

/* filters */
.filters{position:absolute;left:98px;top:657px;width:267px;height:567px;background:var(--panel);font-size:12px;color:#444}
.filters h3{position:absolute;left:17px;top:12px;font-size:20px;font-weight:400;color:var(--orange)}
.filters .label{position:absolute;left:20px}
.slider-track{position:absolute;left:20px;top:75px;width:223px;height:10px;border-radius:5px;background:#cfcfcf}
.slider-fill{position:absolute;left:0;top:0;width:80px;height:10px;border-radius:5px;background:var(--orange)}
.slider-knob{position:absolute;left:69px;top:-6px;width:24px;height:24px;border-radius:50%;background:var(--orange)}
.select{position:absolute;left:20px;width:230px;height:36px;background:var(--white);border:1px solid #e4e4e4;box-shadow:inset 0 0 6px rgba(0,0,0,.08);padding:10px 12px;font-size:11.5px}
.select svg{position:absolute;right:14px;top:14px}
.opt{position:absolute;display:flex;align-items:center;gap:9px;font-size:11.5px}
.radio{width:14px;height:14px;border-radius:50%;border:1px solid #999;background:var(--white)}
.check{width:15px;height:15px;border:1px solid #999;background:var(--white)}
.filters .btn{position:absolute;left:23px;top:507px;width:96px;height:36px;font-size:11px}

/* projects */
.section-title{position:absolute;font-size:21px;font-weight:400;color:var(--orange)}
.sort{position:absolute;left:970px;top:657px;font-size:15px;color:#444}
.sort-btn{position:absolute;left:1021px;top:652px;width:80px;height:31px;background:#e9e9e9;border-radius:2px;font-size:13px;color:#666;padding:6px 0 0 15px}
.sort-btn svg{position:absolute;right:12px;top:13px}
.card{position:absolute;width:346px;height:198px;background:#f7f7f7;border:1px solid var(--line);border-radius:3px}
.avatar{position:absolute;left:20px;top:18px;width:74px;height:74px;border-radius:50%;background:radial-gradient(circle at 50% 40%,#9a8f88,#4a4240 70%)}
.price{position:absolute;left:0;top:100px;width:114px;text-align:center;font-size:19px;color:var(--orange)}
.period{position:absolute;left:0;top:128px;width:114px;text-align:center;font-size:11px;color:#555}
.card h4{position:absolute;left:109px;top:20px;font-size:21px;font-weight:400;color:#222}
.stars{position:absolute;left:109px;top:54px;display:flex;align-items:center;gap:1px;font-size:13px;color:#555}
.stars span{margin-left:14px}
.card p{position:absolute;left:109px;top:88px;width:220px;font-size:11px;line-height:19.5px;color:#666;text-align:justify}

/* testimonials */
.arrows{position:absolute;left:1064px;top:1384px;display:flex;gap:8px}
.quote{position:absolute;top:1437px;width:496px;height:208px;background:#f0f0f0;border-radius:3px;padding:20px 27px;font-size:11.5px;line-height:20.5px;color:#666}
.quote p+p{margin-top:18px}
.quote .mark{float:left;margin:0 10px 0 0}
.quote-tail{position:absolute;top:208px;left:349px;width:0;height:0;border-left:14px solid transparent;border-right:14px solid transparent;border-top:30px solid #f0f0f0}
.author{position:absolute;top:1690px;font-size:14px;font-style:italic;color:#333}

/* clients */
.client{position:absolute;top:1784px;width:187px;height:98px;border:3px solid #dedede;display:flex;align-items:center;justify-content:center;gap:10px;font-size:24px;font-weight:600;color:#bdbdbd}
.client .sq{width:20px;height:20px;background:#c9c9c9}

/* contact band */
.band{position:absolute;left:0;top:1931px;width:1200px;height:91px;background:var(--orange);display:flex}
.band-item{height:91px;display:flex;align-items:center;gap:16px;font-size:21px;color:var(--white)}
.band-icon{width:44px;height:44px;border-radius:50%;background:var(--white);display:flex;align-items:center;justify-content:center}
.band-divider{width:1px;height:91px;background:rgba(255,255,255,.45)}

/* footer */
.site-footer{position:absolute;left:0;top:2022px;width:1200px;height:211px;background:var(--dark-2);color:#aaa}
.footer-brand{left:98px;top:40px;font-size:34px}
.footer-brand .brand-dot{width:52px;height:52px}
.footer-col{position:absolute;top:45px}
.footer-col h5{font-size:21px;font-weight:400;color:var(--white);margin-bottom:10px}
.footer-col a{display:block;font-size:12px;color:#aaa;text-decoration:none;line-height:26px}
.social{position:absolute;left:692px;top:47px;display:flex;gap:7px}
.social i{width:28px;height:28px;border-radius:50%;background:#8a8a8a}
.legal{position:absolute;left:694px;top:92px;font-size:12px;color:#aaa;display:flex;gap:18px}
.legal span:first-child{margin-right:6px}
</style>
</head>
<body>

<header class="site-header">
  <div class="search">Search
    <svg width="13" height="13" viewBox="0 0 13 13"><circle cx="5.5" cy="5.5" r="4.2" fill="none" stroke="#222" stroke-width="1.8"/><line x1="8.5" y1="8.5" x2="12" y2="12" stroke="#222" stroke-width="2"/></svg>
  </div>
  <div class="notice"><span class="notice-tag">Notification</span>Neque porro quisquam est, qui dolorem ipsum quia dolor sit amet, consectetur, adipisci velit</div>
  <nav class="nav">
    <a class="active" href="#">Home</a>
    <a href="#">Projects</a>
    <a href="#">How it Works</a>
    <a href="#">Plans</a>
    <a href="#">My Account</a>
  </nav>
  <div class="brand header-brand">pelmora<span class="brand-dot"></span></div>
</header>

<section class="hero">
  <div class="hero-shade" role="img" aria-label="Photo of a team working together around a wooden table with laptops, charts and coffee"></div>
  <h1>Convert More Customers</h1>
  <p>Experience the power of experts collaborating on your project.</p>
  <a class="btn" href="#">GET STARTED</a>
  <div class="dots"><i></i><i class="on"></i><i></i></div>
</section>

<aside class="filters">
  <h3>Filters</h3>
  <div class="label" style="top:56px">Price</div>
  <div class="slider-track"><div class="slider-fill"></div><div class="slider-knob"></div></div>
  <div class="label" style="top:95px">$20</div>
  <div class="label" style="top:95px;left:205px">$1,000+</div>
  <div class="label" style="top:134px">Country</div>
  <div class="select" style="top:165px">Select<svg width="9" height="6" viewBox="0 0 9 6"><path d="M1 1l3.5 3.5L8 1" fill="none" stroke="#555" stroke-width="1.4"/></svg></div>
  <div class="label" style="top:220px">Categories</div>
  <div class="select" style="top:251px">Select<svg width="9" height="6" viewBox="0 0 9 6"><path d="M1 1l3.5 3.5L8 1" fill="none" stroke="#555" stroke-width="1.4"/></svg></div>
  <div class="label" style="top:305px">Time Left</div>
  <div class="opt" style="left:20px;top:333px"><span class="radio"></span>Active</div>
  <div class="opt" style="left:95px;top:333px"><span class="radio"></span>Expired</div>
  <div class="opt" style="left:20px;top:365px"><span class="check"></span>Contains adult content</div>
  <div class="label" style="top:398px">Followers</div>
  <div class="opt" style="left:20px;top:425px"><span class="check"></span>Friendloop</div>
  <div class="opt" style="left:20px;top:450px"><span class="check"></span>Chirpline</div>
  <div class="opt" style="left:20px;top:475px"><span class="check"></span>Rss</div>
  <a class="btn" href="#">SAVE FILTERS</a>
</aside>

<h2 class="section-title" style="left:390px;top:656px">Crowd Projects:</h2>
<div class="sort">Sort</div>
<div class="sort-btn">Price<svg width="8" height="5" viewBox="0 0 8 5"><path d="M1 1l3 3 3-3" fill="none" stroke="#666" stroke-width="1.3"/></svg></div>

<svg width="0" height="0" style="position:absolute">
  <defs><path id="star" d="M6 0l1.8 3.9 4.2.4-3.2 2.8.9 4.1L6 9.1 2.3 11.2l.9-4.1L0 4.3l4.2-.4z" fill="#f7931e"/></defs>
</svg>

<article class="card" style="left:395px;top:715px">
  <div class="avatar" role="img" aria-label="Portrait photo of the project expert"></div>
  <div class="price">$80</div><div class="period">monthly</div>
  <h4>Morbi in ante arcu</h4>
  <div class="stars"><svg width="74" height="12"><use href="#star"/><use href="#star" x="15"/><use href="#star" x="30"/><use href="#star" x="45"/><use href="#star" x="60"/></svg><span>9 Reviews</span></div>
  <p>Neque porro quisquam est, qui dolorem ipsum quia dolor sit amet, consectetur, adipisci velit, sed quia non numquam eius modi tempora incidunt</p>
</article>
<article class="card" style="left:756px;top:715px">
  <div class="avatar" role="img" aria-label="Portrait photo of the project expert"></div>
  <div class="price">$90</div><div class="period">monthly</div>
  <h4>Morbi in ante arcu</h4>
  <div class="stars"><svg width="74" height="12"><use href="#star"/><use href="#star" x="15"/><use href="#star" x="30"/><use href="#star" x="45"/><use href="#star" x="60"/></svg><span>9 Reviews</span></div>
  <p>Neque porro quisquam est, qui dolorem ipsum quia dolor sit amet, consectetur, adipisci velit, sed quia non numquam eius modi tempora incidunt</p>
</article>
<article class="card" style="left:395px;top:932px">
  <div class="avatar" role="img" aria-label="Portrait photo of the project expert"></div>
  <div class="price">$80</div><div class="period">monthly</div>
  <h4>Morbi in ante arcu</h4>
  <div class="stars"><svg width="74" height="12"><use href="#star"/><use href="#star" x="15"/><use href="#star" x="30"/><use href="#star" x="45"/><use href="#star" x="60"/></svg><span>9 Reviews</span></div>
  <p>Neque porro quisquam est, qui dolorem ipsum quia dolor sit amet, consectetur, adipisci velit, sed quia non numquam eius modi tempora incidunt</p>
</article>
<article class="card" style="left:756px;top:932px">
  <div class="avatar" role="img" aria-label="Portrait photo of the project expert"></div>
  <div class="price">$90</div><div class="period">monthly</div>
  <h4>Morbi in ante arcu</h4>
  <div class="stars"><svg width="74" height="12"><use href="#star"/><use href="#star" x="15"/><use href="#star" x="30"/><use href="#star" x="45"/><use href="#star" x="60"/></svg><span>9 Reviews</span></div>
  <p>Neque porro quisquam est, qui dolorem ipsum quia dolor sit amet, consectetur, adipisci velit, sed quia non numquam eius modi tempora incidunt</p>
</article>
<article class="card" style="left:395px;top:1148px">
  <div class="avatar" role="img" aria-label="Portrait photo of the project expert"></div>
  <div class="price">$80</div><div class="period">monthly</div>
  <h4>Morbi in ante arcu</h4>
  <div class="stars"><svg width="74" height="12"><use href="#star"/><use href="#star" x="15"/><use href="#star" x="30"/><use href="#star" x="45"/><use href="#star" x="60"/></svg><span>9 Reviews</span></div>
  <p>Neque porro quisquam est, qui dolorem ipsum quia dolor sit amet, consectetur, adipisci velit, sed quia non numquam eius modi tempora incidunt</p>
</article>

<h2 class="section-title" style="left:101px;top:1378px">Testimonials</h2>
<div class="arrows">
  <svg width="14" height="22" viewBox="0 0 14 22"><path d="M11 3L4 11l7 8" fill="none" stroke="#cfcfcf" stroke-width="3"/></svg>
  <svg width="14" height="22" viewBox="0 0 14 22"><path d="M3 3l7 8-7 8" fill="none" stroke="#cfcfcf" stroke-width="3"/></svg>
</div>

<div class="quote" style="left:98px">
  <svg class="mark" width="38" height="28" viewBox="0 0 38 28"><path d="M0 28V14C0 6 4 1 12 0v5c-4 1-6 4-6 8h6v15zM21 28V14c0-8 4-13 12-14v5c-4 1-6 4-6 8h6v15z" fill="#d9d9d9"/></svg>
  <p>Neque porro quisquam est, qui dolorem ipsum quia dolor sit amet, consectetur, adipisci velit, sed quia non numquam eius modi tempora incidunt</p>
  <p>Ut enim ad minima veniam, quis nostrum exercitationem ullam corporis suscipit laboriosam, nisi ut aliquid ex ea commodi consequatur? Quis autem vel eum iure reprehenderit qui in ea voluptate velit esse quam nihil</p>
  <span class="quote-tail"></span>
</div>
<div class="quote" style="left:607px">
  <svg class="mark" width="38" height="28" viewBox="0 0 38 28"><path d="M0 28V14C0 6 4 1 12 0v5c-4 1-6 4-6 8h6v15zM21 28V14c0-8 4-13 12-14v5c-4 1-6 4-6 8h6v15z" fill="#d9d9d9"/></svg>
  <p>Neque porro quisquam est, qui dolorem ipsum quia dolor sit amet, consectetur, adipisci velit, sed quia non numquam eius modi tempora incidunt</p>
  <p>Ut enim ad minima veniam, quis nostrum exercitationem ullam corporis suscipit laboriosam, nisi ut aliquid ex ea commodi consequatur? Quis autem vel eum iure reprehenderit qui in ea voluptate velit esse quam nihil</p>
  <span class="quote-tail"></span>
</div>
<div class="author" style="left:418px">- John Doe -</div>
<div class="author" style="left:927px">- John Doe -</div>

<h2 class="section-title" style="left:98px;top:1736px">Our clients</h2>
<div class="client" style="left:98px"><span class="sq"></span>Norvane</div>
<div class="client" style="left:299px">Kestrel</div>
<div class="client" style="left:505px">Valdria</div>
<div class="client" style="left:710px">Orbix</div>
<div class="client" style="left:916px">Tamsen</div>

<section class="band">
  <div class="band-item" style="width:441px;padding-left:217px">
    <span class="band-icon"><svg width="20" height="20" viewBox="0 0 20 20"><path d="M5 2l3 4-2 2c1 2 3 4 5 5l2-2 4 3-2 3C9 17 3 11 2 5z" fill="#f7931e"/></svg></span>Contact Us
  </div>
  <span class="band-divider"></span>
  <div class="band-item" style="width:325px;padding-left:34px">
    <span class="band-icon"><svg width="22" height="22" viewBox="0 0 22 22"><circle cx="11" cy="11" r="10" fill="#f7931e"/><path d="M6 8c2-2 5-1 6 1s-1 3 1 5 3 0 3-2M9 16c0-2-2-2-3-3" fill="none" stroke="#fff" stroke-width="1.6"/></svg></span>Ask the Community
  </div>
  <span class="band-divider"></span>
  <div class="band-item" style="padding-left:33px">
    <span class="band-icon"><svg width="22" height="20" viewBox="0 0 22 20"><rect x="1" y="1" width="20" height="13" rx="1.5" fill="#f7931e"/><rect x="4" y="4" width="14" height="7" fill="#fff"/><rect x="9" y="14" width="4" height="3" fill="#f7931e"/><rect x="6" y="17" width="10" height="2" fill="#f7931e"/></svg></span>Get the Demo
  </div>
</section>

<footer class="site-footer">
  <div class="brand footer-brand">pelmora<span class="brand-dot"></span></div>
  <div class="footer-col" style="left:411px">
    <h5>General</h5>
    <a href="#">FAQ</a><a href="#">Our Team</a><a href="#">Email Us</a>
  </div>
  <div class="footer-col" style="left:548px">
    <h5>Company</h5>
    <a href="#">News Room</a><a href="#">Resources</a><a href="#">Jobs</a><a href="#">Online Communities</a>
  </div>
  <div class="social"><i></i><i></i><i></i><i></i><i></i><i></i></div>
  <div class="legal"><span>© 2015 pelmora.com</span><span>Site Map</span><span>Privacy</span><span>Security</span><span>Disclaimer</span></div>
</footer>

</body>
</html>
```